Plakate für Haushaltshilfen und Alltagsbegleiter
Zielgruppe
Wir bieten haushaltsnahe Dienstleistungen (Haushaltshilfen und Altgasbegleiter) für Personen mit einem Pflegegrad 1 - 5 an.
Zielgruppe sind Personen mit einem Pflegegrad 1 - 5. Hauptsächlich ältere Menschen die Unterstützung/Betreuung im Alltag und Haushalt benötigen.
Aufgabenstellung
Wir benötigen für unsere Büroräume eine Fensterbeschriftung. Es handelt sich hier um 5 Fenster (Glasflächen) und eine Glastür. Die Vorgabe ist, dass von außen zu erkennen ist dass sich um alle Räumlichkeiten um unsere (Firma Lindwerk) Räumlichkeiten handelt. Desweiteren soll auch unser Angebot erkennbar sein.
Unser Angebot enthält: Haushaltshilfen und Alltagsbegleiter
- kostenlose Haushaltshilfe ab Pflegegrad 1
- Abrechnung mit allen Kostenträgern
Da wir keine Schilder an die Fassade anbringen können, müßen die Glasflächen dafür genutzt werden um zum Einen uns als Firma erkennbar zu machen und zum anderen unser Angebot kurz zu präsentieren.
Uns ist wichtig dass unser Logo verwendet wir und auch unsere Farben.
Desweiteren sollten an den Fenstern auch teilweise eine Sichtschutz nach innen, angebracht werden, aber eben nur teilweise also nicht das ganzen Fenster z.Bsp. mit einer Blickdichten Folie überziehen, sondern in Augenhöhe wenn Fußgänger vorbei laufen.

```html
<!DOCTYPE html>
<html lang="de">
<head>
<meta charset="utf-8">
<title>Lindwerk – Fensterbeschriftung</title>
<link href="https://fonts.googleapis.com/css2?family=Montserrat:wght@600;700;800&family=Raleway:wght@400;500&display=swap" rel="stylesheet">
<style>
  :root{
    --stage:#ababab;
    --red:#c1272d;
    --red-dark:#8f1d1d;
    --dark:#3a3a3c;
    --grey:#a7a7a7;
    --white:#ffffff;
    --ink:#333333;
    --head:'Montserrat', Arial, sans-serif;
    --body:'Raleway', Arial, sans-serif;
  }
  *{margin:0;padding:0;box-sizing:border-box}
  html,body{width:1200px;height:393px;overflow:hidden;background:var(--stage)}
  .wall{position:relative;width:1200px;height:393px}
  .poster{position:absolute;overflow:hidden;background:var(--white)}
  .poster svg.shapes{position:absolute;left:0;top:0;width:100%;height:100%}
  .photo{position:absolute}
  .brand{position:absolute;left:0;right:0;display:flex;align-items:center;justify-content:center;gap:5px;font-family:var(--head);font-weight:700;letter-spacing:1px}
  .brand .dot{border-radius:50%;flex:none}
  .brand.red{color:var(--red)} .brand.red .dot{background:var(--red)}
  .brand.light{color:var(--white)} .brand.light .dot{background:var(--white)}

  /* Poster 1 */
  .p1{left:30px;top:37px;width:200px;height:272px}
  .p1 .band{position:absolute;left:0;top:72px;width:200px;height:19px;background:var(--dark);color:var(--white);font:800 12.5px var(--head);text-align:center;line-height:19px;letter-spacing:.3px}
  .benefit{position:absolute;width:90px;text-align:center;font:500 6px/7.3px var(--body);color:var(--ink)}
  .benefit .icon{width:32px;height:32px;margin:0 auto 3px;background:var(--red);border-radius:3px;display:flex;align-items:center;justify-content:center}

  /* Poster 2 */
  .p2{left:236px;top:37px;width:200px;height:272px}
  .p2 .claim{position:absolute;left:10px;right:10px;top:229px;color:var(--white);font:800 8.3px/11px var(--head);text-align:center}

  /* Poster 3 */
  .p3{left:444px;top:37px;width:200px;height:272px}
  .p3 .headline{position:absolute;right:15px;top:77px;text-align:right;color:var(--red);font:800 12.2px/15px var(--head)}

  .tag{position:absolute;background:var(--red);color:var(--white);font:800 6.2px/7.5px var(--head);text-align:center;border-radius:4px;padding:4px 8px}

  /* Poster 4 */
  .p4{left:651px;top:35px;width:172px;height:276px}
  .privacy{position:absolute;background:#000}

  /* Poster 5 */
  .p5{left:833px;top:35px;width:146px;height:325px;border:1px solid #555}
  .p5 .intro{position:absolute;left:15px;top:121px;width:120px;color:var(--white);font:800 6.6px/9px var(--head)}

  /* Poster 6 */
  .p6{left:986px;top:35px;width:172px;height:276px;background:var(--dark)}
  .p6 .cta{position:absolute;left:0;right:0;top:184px;text-align:center;color:var(--white);font:500 9px var(--body)}
  .p6 .phone{position:absolute;left:16px;width:140px;top:202px;height:22px;background:var(--red);border-radius:4px;color:var(--white);font:800 13.5px/22px var(--head);text-align:center;letter-spacing:.3px}
  .p6 .web{position:absolute;left:0;right:0;top:229px;text-align:center;color:var(--white);font:500 12px var(--body)}
</style>
</head>
<body>
<main class="wall">

  <!-- Poster 1: Vorteile -->
  <section class="poster p1">
    <svg class="shapes" viewBox="0 0 200 272" preserveAspectRatio="none">
      <polygon points="0,225 110,272 0,272" fill="var(--red-dark)"/>
      <polygon points="200,198 200,232 70,272 50,272" fill="var(--red)"/>
      <polygon points="200,232 200,272 70,272" fill="var(--dark)"/>
    </svg>
    <div class="brand red" style="top:30px;font-size:12px"><span class="dot" style="width:10px;height:10px"></span>LINDWERK</div>
    <div class="band">UNSERE VORTEILE</div>
    <div class="benefit" style="left:5px;top:98px">
      <div class="icon"><svg width="16" height="18" viewBox="0 0 16 18"><path d="M2 1h8l4 4v12H2z" fill="#fff"/><text x="8" y="14" font-size="8" font-family="Arial" font-weight="700" fill="var(--red)" text-anchor="middle">$</text></svg></div>
      Abrechnung mit allen Pflegekassen möglich
    </div>
    <div class="benefit" style="left:101px;top:98px">
      <div class="icon"><svg width="18" height="18" viewBox="0 0 18 18"><path d="M7 1h4v4h4v4h-4v4H7V9H3V5h4z" fill="#fff"/><path d="M1 15h4l4 1 7-3v2l-7 3H1z" fill="#fff"/></svg></div>
      Abrechnung über den Entlastungsbetrag von mind. 125 € mtl. ab Pflegegrad 1 möglich
    </div>
    <div class="benefit" style="left:5px;top:165px">
      <div class="icon"><svg width="18" height="18" viewBox="0 0 18 18"><path d="M9 11C4 7 3 5 5 3s4 0 4 1c0-1 2-3 4-1s1 4-4 8z" fill="#fff"/><path d="M1 14h4l4 1 7-3v2l-7 3H1z" fill="#fff"/></svg></div>
      Auch über die Verhinderungspflege
    </div>
    <div class="benefit" style="left:101px;top:165px">
      <div class="icon"><svg width="18" height="18" viewBox="0 0 18 18"><path d="M2 1h8l4 4v12H2z" fill="#fff"/><path d="M4 12l2-3 2 2 2-4" stroke="var(--red)" stroke-width="1.3" fill="none"/><path d="M11 12l6-6 1 1-6 6-2 1z" fill="#fff" stroke="var(--red)" stroke-width=".6"/></svg></div>
      Hilfe bei der Antragsstellung
    </div>
  </section>

  <!-- Poster 2: Paar -->
  <section class="poster p2">
    <div class="photo" role="img" aria-label="Foto eines lachenden älteren Paares" style="left:0;top:0;width:200px;height:230px;background:linear-gradient(180deg,#f7f7f7 0%,#eceae8 30%,#c9b8a8 60%,#6e6a6c 100%)"></div>
    <svg class="shapes" viewBox="0 0 200 272" preserveAspectRatio="none">
      <polygon points="0,195 90,190 200,225 200,272 0,272" fill="var(--red)"/>
      <polygon points="0,210 90,200 160,222 200,212 200,272 0,272" fill="var(--dark)"/>
    </svg>
    <div class="brand red" style="top:52px;font-size:11px"><span class="dot" style="width:10px;height:10px"></span>LINDWERK</div>
    <p class="claim">WIR BIETEN HAUSHALTSHILFEN UND ALLTAGSBEGLEITER FÜR PRIVATHAUSHALTE AN.</p>
  </section>

  <!-- Poster 3: Angebot -->
  <section class="poster p3">
    <div class="photo" role="img" aria-label="Foto eines älteren Mannes mit Frau und Kind auf dem Sofa" style="left:0;top:112px;width:200px;height:160px;background:linear-gradient(160deg,#f4f4f4 0%,#d9c8b8 40%,#9aa8bd 75%,#c8d0dc 100%)"></div>
    <svg class="shapes" viewBox="0 0 200 272" preserveAspectRatio="none">
      <polygon points="0,0 200,0 200,10 0,92" fill="var(--red)"/>
      <polygon points="130,0 200,0 200,38 145,8" fill="var(--dark)"/>
    </svg>
    <div class="brand red" style="top:48px;left:70px;right:15px;justify-content:flex-end;font-size:13px"><span class="dot" style="width:12px;height:12px"></span>LINDWERK</div>
    <h2 class="headline">HAUSHALTSHILFEN UND<br>ALLTAGSBEGLEITER</h2>
    <div class="tag" style="left:97px;top:222px;transform:rotate(-8deg)">KOSTENLOSE<br>HAUSHALTSHILFE<br>AB PFLEGEGRAD 1</div>
  </section>

  <!-- Poster 4: Abrechnung -->
  <section class="poster p4">
    <div class="photo" role="img" aria-label="Foto einer älteren Hand auf einem Gehstock" style="left:0;top:90px;width:172px;height:186px;background:linear-gradient(180deg,#f2f2f2 0%,#d8d4d0 45%,#a9b7b3 75%,#7b8c88 100%)"></div>
    <svg class="shapes" viewBox="0 0 172 276" preserveAspectRatio="none">
      <polygon points="0,0 172,0 172,62 128,100 55,68 0,78" fill="var(--dark)"/>
      <polygon points="0,78 55,68 128,100 172,62 172,95 128,105 90,95 0,100" fill="var(--red)"/>
    </svg>
    <div class="brand light" style="top:30px;font-size:11px"><span class="dot" style="width:11px;height:11px"></span>LINDWERK</div>
    <div class="privacy" style="left:48px;top:101px;width:76px;height:44px"></div>
    <div class="tag" style="left:82px;top:153px;transform:rotate(-8deg)">ABRECHNUNG MIT<br>ALLEN<br>KOSTENTRÄGERN</div>
  </section>

  <!-- Poster 5: Tür -->
  <section class="poster p5">
    <svg class="shapes" viewBox="0 0 146 325" preserveAspectRatio="none">
      <polygon points="0,15 146,15 146,300 0,300" fill="var(--grey)"/>
      <polygon points="0,0 112,0 0,70" fill="var(--red)"/>
      <polygon points="112,0 146,0 146,15 70,15" fill="var(--white)"/>
      <polygon points="0,285 60,285 100,305 146,280 146,300 100,312 60,300 0,308" fill="var(--red)"/>
      <polygon points="0,308 60,300 100,312 146,300 146,325 0,325" fill="var(--white)"/>
    </svg>
    <div class="brand light" style="top:92px;font-size:10px"><span class="dot" style="width:11px;height:11px"></span>LINDWERK</div>
    <p class="intro">DEN ALLTAG ZU BEWÄLTIGEN KANN EINE ECHTE HERAUSFORDERUNG SEIN. EGAL OB SIE HILFE BEIM EINKAUFEN ODER ANDEREN ALLTÄGLICHEN AKTIVITÄTEN BENÖTIGEN, WIR HELFEN GERNE.</p>
  </section>

  <!-- Poster 6: Kontakt -->
  <section class="poster p6">
    <div class="photo" role="img" aria-label="Foto zweier Hände, die ein Herz aus Papier halten" style="left:0;top:0;width:172px;height:170px;background:linear-gradient(180deg,#b9d3e0 0%,#d9c5b6 35%,#c4d9e4 70%,#eef3f6 100%)"></div>
    <svg class="shapes" viewBox="0 0 172 276" preserveAspectRatio="none">
      <polygon points="0,145 45,142 100,170 172,140 172,163 100,180 45,165 0,170" fill="var(--red)"/>
      <polygon points="0,170 45,165 100,180 172,163 172,276 0,276" fill="var(--dark)"/>
    </svg>
    <div class="privacy" style="left:48px;top:101px;width:76px;height:44px"></div>
    <p class="cta">Buchen Sie gleich einen Termin:</p>
    <div class="phone">0711 20 38 57 19</div>
    <p class="web">www.lindwerk.de</p>
  </section>

</main>
</body>
</html>
```